Dusty Spur Outfitters Home Page

I need a logo and page design for my home page, maybe some background color suggestions to go with it. I want the logo to project "vintage" and "western wear" but not be your typical trite western saddle and gun type thing.
http://www.dustyspuroutfitters.example/store/cart.php
Not looking for page coding just logo and other design elements to lay in over the site's template to make it "pop"
Reason: Have to finalize the design.
Target Market(s)
My customers are 70/30 men to women.
Industry/Entity Type
Gun

```html
<!DOCTYPE html>
<html lang="en">
<head>
<meta charset="utf-8">
<title>Dusty Spur Outfitters – Home</title>
<link href="https://fonts.googleapis.com/css2?family=Kaushan+Script&family=Montserrat:wght@400;500;600;700;800&display=swap" rel="stylesheet">
<style>
:root{
  --red:#e3192f;
  --red-dark:#b5101f;
  --ink:#0b0b0b;
  --panel:#151515;
  --card:#0f0f0f;
  --card-line:#2c2c2c;
  --text:#d6d6d6;
  --muted:#7a7a7a;
  --white:#ffffff;
}
*{box-sizing:border-box;margin:0;padding:0}
html,body{width:682px;height:1200px;overflow:hidden;background:var(--ink)}
body{position:relative;font-family:"Montserrat",sans-serif;color:var(--text)}
.abs{position:absolute}
.script{font-family:"Kaushan Script",cursive}

.hero-bg{left:0;top:0;width:682px;height:500px;background:linear-gradient(180deg,#2a2a2a 0%,#3a3a3a 30%,#262626 60%,#151515 100%)}
.body-bg{left:0;top:500px;width:682px;height:492px;background:linear-gradient(180deg,#151515,#1b1b1b 50%,#121212)}
.footer-bg{left:0;top:992px;width:682px;height:208px;background:#050505}

.welcome{left:76px;top:13px;font-size:7px;font-style:italic;color:#bdbdbd;letter-spacing:.2px;white-space:nowrap}
.cart-box{left:428px;top:10px;width:146px;height:17px;border:1px solid #555;background:#1e1e1e;font-size:6.5px;font-style:italic;color:#ddd;display:flex;align-items:center;padding-left:6px;gap:4px;white-space:nowrap;overflow:hidden}
.cart-box .count{color:var(--red)}
.search-box{left:582px;top:10px;width:24px;height:17px;border:1px solid #555;background:#1e1e1e}

.brand{left:0;top:82px;width:682px;text-align:center;font-weight:800;font-size:24px;letter-spacing:1px;color:var(--white);white-space:nowrap}
.brand-rule{left:260px;top:141px;width:162px;height:1px;background:#555}

.nav{left:0;top:160px;width:682px;height:20px}
.nav a{position:absolute;font-family:"Kaushan Script",cursive;font-size:13px;color:var(--white);text-decoration:none;white-space:nowrap}
.nav a.active{color:var(--red)}

.main-panel{left:74px;top:210px;width:532px;height:286px;background:#101010}
.cat-head{left:74px;top:210px;width:125px;height:24px;background:#2b2b2b;text-align:center;font-size:12px;line-height:24px;color:var(--white);white-space:nowrap}
.cat-head::before,.cat-head::after{content:"";display:inline-block;width:14px;height:1.5px;background:var(--red);vertical-align:middle;margin:0 5px}
.cat-list{left:84px;top:239px;list-style:none}
.cat-list li{height:14.9px;font-size:7.5px;color:#d0d0d0;display:flex;align-items:center;gap:5px;white-space:nowrap}
.cat-list li::before{content:"";width:6px;height:6px;border-radius:50%;background:var(--red);box-shadow:inset 0 0 0 1.5px var(--red),inset 0 0 0 3px #fff}
.banner{left:210px;top:220px;width:388px;height:266px;background:linear-gradient(135deg,#4a4444,#2f2b2b 60%,#242121)}
.banner-photo{left:210px;top:220px;width:215px;height:266px;background:linear-gradient(180deg,#5a4c40 0%,#6d7588 35%,#556075 70%,#3c4150 100%);opacity:.85}
.promo{left:420px;width:180px;text-align:center;white-space:nowrap}
.promo-pct{top:288px;font-size:46px;font-weight:800;color:var(--red);letter-spacing:-1px}
.promo-word{top:346px;font-size:29px;font-weight:800;color:#bdbdbd}
.promo-date{top:382px;font-size:16px;color:var(--white)}
.promo-code{left:380px;top:419px;width:215px;text-align:right;font-size:12px;color:#ddd;white-space:nowrap}
.promo-code b{color:var(--red);font-family:"Montserrat",sans-serif;font-weight:800;font-size:11px}
.slider-arrow{top:452px;width:20px;height:20px;border-radius:50%;background:#555;display:flex;align-items:center;justify-content:center}

.section-title{left:0;top:509px;width:682px;text-align:center;font-size:12px;color:var(--white);font-weight:400}
.section-title::before,.section-title::after{content:"";display:inline-block;width:18px;height:1.5px;background:var(--red);vertical-align:middle;margin:0 6px}

.card{width:121px;height:167px;background:var(--card);border:1px solid var(--card-line)}
.card .photo{position:absolute;left:22px;top:8px;width:77px;height:100px;border-radius:3px}
.card .name{position:absolute;left:0;top:114px;width:100%;text-align:center;font-size:7.5px;font-weight:500;color:#e0e0e0;white-space:nowrap}
.card .desc{position:absolute;left:0;top:126px;width:100%;text-align:center;font-size:5.5px;color:var(--muted);white-space:nowrap}
.card .price{position:absolute;left:12px;top:147px;font-size:6.5px;color:var(--red)}
.card .add{position:absolute;left:61px;top:143px;width:49px;height:14px;background:#3a3a3a;border:1px solid #555;font-size:6px;color:#eee;text-align:center;line-height:12px;white-space:nowrap}

.view-all{left:280px;top:918px;width:121px;height:23px;background:var(--red);text-align:center;font-size:11px;line-height:23px;color:var(--white);white-space:nowrap}

.feature-bar{left:74px;top:970px;width:532px;height:42px;background:var(--red)}
.feature{top:978px;width:121px;height:26px;border:1px solid #fff;display:flex;align-items:center;justify-content:center;gap:8px;font-size:10.5px;color:var(--white);white-space:nowrap}

.col-head{top:1032px;font-size:10px;color:var(--white);font-weight:400;white-space:nowrap}
.links{top:1052px;list-style:none}
.links li{height:13.3px;font-size:7.5px;color:#c4c4c4;white-space:nowrap}
.news-text{left:460px;top:1052px;width:150px;font-size:7px;line-height:9.5px;color:#c4c4c4}
.news-input{left:460px;top:1082px;width:144px;height:20px;background:#111;border:1px solid #222;font-size:6px;color:#999;padding-left:5px;line-height:18px}
.subscribe{left:460px;top:1112px;width:144px;height:17px;border:1px solid #ddd;text-align:center;font-size:6.5px;line-height:15px;color:var(--red);font-weight:600}

.legal{left:73px;top:1162px;font-size:5.5px;line-height:11px;color:#aaa;white-space:nowrap}
.pay{top:1169px;font-size:8px;font-weight:700;color:#444;white-space:nowrap}
.badge{left:389px;top:1165px;width:48px;height:15px;background:#3a3a3a;border-radius:2px}
.social{top:1160px;width:25px;height:25px;border-radius:50%;border:1px solid #444;display:flex;align-items:center;justify-content:center;font-size:4.5px;color:#ccc;white-space:nowrap}
</style>
</head>
<body>

<div class="abs hero-bg" role="img" aria-label="Dark night photograph of mountain cliffs and a pine forest behind the header"></div>
<div class="abs body-bg" role="img" aria-label="Dark background with a subtle swirling pattern"></div>
<div class="abs footer-bg"></div>

<p class="abs welcome">Welcome visitor you can login or create an account.</p>
<div class="abs cart-box">
  <svg width="10" height="9" viewBox="0 0 10 9"><path d="M0 1h2l1.5 5h5L10 2H3" fill="none" stroke="#ccc" stroke-width="1"/><circle cx="4" cy="8" r=".9" fill="#ccc"/><circle cx="8" cy="8" r=".9" fill="#ccc"/></svg>
  <span>Shopping Cart <span class="count">0 item(s)</span> - $0.00</span>
  <svg width="6" height="4" viewBox="0 0 6 4" style="margin-left:2px"><path d="M0 0l3 3 3-3" fill="none" stroke="#ccc"/></svg>
</div>
<div class="abs search-box">
  <svg width="22" height="15" viewBox="0 0 22 15"><circle cx="6" cy="6" r="3" fill="none" stroke="#fff" stroke-width="1.3"/><path d="M8 8l3 3" stroke="#fff" stroke-width="1.5"/><path d="M14 6l2.5 2.5L19 6" fill="none" stroke="#ccc"/></svg>
</div>

<div class="abs brand">Dusty Spur Outfitters</div>
<div class="abs brand-rule"></div>

<nav class="abs nav">
  <a class="active" style="left:83px">Home</a>
  <a style="left:134px">About Us</a>
  <a style="left:214px">Products</a>
  <a style="left:289px">Shipping</a>
  <a style="left:365px">Returns</a>
  <a style="left:429px">Sizing</a>
  <a style="left:484px">Links</a>
  <a style="left:537px">Contact Us</a>
</nav>

<div class="abs main-panel"></div>
<div class="abs cat-head script">Categories</div>
<ul class="abs cat-list">
  <li>Boots</li><li>Men's Western Wear</li><li>Women's Western Wear</li><li>Brand New Arrivals</li>
  <li>CLEARANCE</li><li>T-Shirts</li><li>Vests</li><li>Accessories</li><li>Jackets</li><li>BELTS</li>
  <li>Hand Bags</li><li>Leather</li><li>On Sale!</li><li>Pants</li><li>Short Sleeves</li><li>Big and Tall</li><li>Jeans</li>
</ul>

<div class="abs banner"></div>
<div class="abs banner-photo" role="img" aria-label="Photo of a man in a brown cowboy hat and patterned western shirt"></div>
<div class="abs promo promo-pct">20%</div>
<div class="abs promo promo-word">Discount</div>
<div class="abs promo promo-date script">Thru June 15th</div>
<div class="abs promo-code script">Use coupon code: <b>OVERSTOCK20</b></div>
<div class="abs slider-arrow" style="left:541px"><svg width="8" height="10" viewBox="0 0 8 10"><path d="M6 1L2 5l4 4" fill="none" stroke="#111" stroke-width="2"/></svg></div>
<div class="abs slider-arrow" style="left:566px"><svg width="8" height="10" viewBox="0 0 8 10"><path d="M2 1l4 4-4 4" fill="none" stroke="#111" stroke-width="2"/></svg></div>

<h2 class="abs section-title script">Our Products</h2>

<div class="abs card" style="left:75px;top:540px"><div class="photo" role="img" aria-label="Fringed suede western jacket" style="background:linear-gradient(180deg,#8a6a3c,#5a4a38 70%,#3b4a6a)"></div><p class="name">Men's Western Wear</p><p class="desc">Donec vehicula nulla vitae</p><span class="price">$120.68</span><span class="add">Add To Cart</span></div>
<div class="abs card" style="left:211px;top:540px"><div class="photo" role="img" aria-label="Tan leather cowboy boot" style="background:linear-gradient(180deg,#3a2a1e,#7a5a3a 60%,#a48a66)"></div><p class="name">Men's Western Wear</p><p class="desc">Donec vehicula nulla vitae</p><span class="price">$120.68</span><span class="add">Add To Cart</span></div>
<div class="abs card" style="left:351px;top:540px"><div class="photo" role="img" aria-label="Dark western suit with white hat" style="background:linear-gradient(180deg,#d8d0c4,#2a2d3a 40%,#1c1e28)"></div><p class="name">Men's Western Wear</p><p class="desc">Donec vehicula nulla vitae</p><span class="price">$120.68</span><span class="add">Add To Cart</span></div>
<div class="abs card" style="left:487px;top:540px"><div class="photo" role="img" aria-label="Leather tote handbag" style="background:linear-gradient(180deg,#141414,#3a2c22 60%,#5a4030)"></div><p class="name">Men's Western Wear</p><p class="desc">Donec vehicula nulla vitae</p><span class="price">$120.68</span><span class="add">Add To Cart</span></div>

<div class="abs card" style="left:75px;top:720px"><div class="photo" role="img" aria-label="Brown fringed leather handbag" style="background:linear-gradient(180deg,#3a2c26,#6e4c3e 50%,#5a3c30)"></div><p class="name">Men's Western Wear</p><p class="desc">Donec vehicula nulla vitae</p><span class="price">$120.68</span><span class="add">Add To Cart</span></div>
<div class="abs card" style="left:211px;top:720px"><div class="photo" role="img" aria-label="Light blue t-shirt" style="background:linear-gradient(180deg,#9fb0c6,#8598b2)"></div><p class="name">Men's Western Wear</p><p class="desc">Donec vehicula nulla vitae</p><span class="price">$120.68</span><span class="add">Add To Cart</span></div>
<div class="abs card" style="left:351px;top:720px"><div class="photo" role="img" aria-label="Red and white cowboy boots" style="background:linear-gradient(180deg,#b8262a,#d84a44 60%,#e8dcd4)"></div><p class="name">Men's Western Wear</p><p class="desc">Donec vehicula nulla vitae</p><span class="price">$120.68</span><span class="add">Add To Cart</span></div>
<div class="abs card" style="left:487px;top:720px"><div class="photo" role="img" aria-label="Tooled leather belts" style="background:linear-gradient(90deg,#6a5032,#b89a78 50%,#6a5032)"></div><p class="name">Men's Western Wear</p><p class="desc">Donec vehicula nulla vitae</p><span class="price">$120.68</span><span class="add">Add To Cart</span></div>

<div class="abs view-all script">View All Products</div>

<div class="abs feature-bar"></div>
<div class="abs feature script" style="left:83px"><svg width="11" height="9" viewBox="0 0 11 9"><rect x="0" y="1" width="7" height="5" fill="#fff"/><path d="M7 3h2l2 2v1H7z" fill="#fff"/><circle cx="2.5" cy="7" r="1.3" fill="#fff"/><circle cx="8.5" cy="7" r="1.3" fill="#fff"/></svg>Specialgift Cards</div>
<div class="abs feature script" style="left:214px"><svg width="10" height="10" viewBox="0 0 10 10"><rect x="0" y="3" width="10" height="2.5" fill="#fff"/><rect x="1" y="6" width="8" height="4" fill="#fff"/><rect x="4.3" y="3" width="1.4" height="7" fill="var(--red)"/></svg>Free Shipping</div>
<div class="abs feature script" style="left:346px"><svg width="10" height="10" viewBox="0 0 10 10"><rect x=".5" y="1.5" width="9" height="8" fill="none" stroke="#fff"/><rect x=".5" y="1.5" width="9" height="2.5" fill="#fff"/></svg>Manufacturers</div>
<div class="abs feature script" style="left:475px"><svg width="11" height="10" viewBox="0 0 11 10"><ellipse cx="5" cy="4" rx="4.5" ry="3.2" fill="none" stroke="#fff"/><path d="M2 6.5L1 9l3-2" fill="#fff"/></svg>Online Support</div>

<h3 class="abs col-head script" style="left:71px">Information</h3>
<ul class="abs links" style="left:71px"><li>Home</li><li>About Us</li><li>Shipping</li><li>Returns</li><li>Sizing Links</li><li>Contact Us</li></ul>
<h3 class="abs col-head script" style="left:194px">Customer Service</h3>
<ul class="abs links" style="left:194px"><li>Contact Us</li><li>Returns</li><li>Site Map</li><li>Specials</li><li>Affiliates</li></ul>
<h3 class="abs col-head script" style="left:332px">My Account</h3>
<ul class="abs links" style="left:332px"><li>My Account</li><li>Order History</li><li>Wish List</li><li>Newsletter</li><li>Brands</li></ul>
<h3 class="abs col-head script" style="left:460px">Newsletter</h3>
<p class="abs news-text">Proin gravida nibh vel velit auctor aliquet.<br>Aenean sollicitudin, lorem quis bibendum</p>
<div class="abs news-input">Enter email address:</div>
<div class="abs subscribe">SUBSCRIBE</div>

<p class="abs legal">@ all copy rights are reserved<br>Powered by: CartForge Shopping Cart Software</p>
<span class="abs pay" style="left:228px">Quillfen</span>
<span class="abs pay" style="left:270px">Brasswick</span>
<span class="abs pay" style="left:316px">Tolvane</span>
<span class="abs pay" style="left:350px;font-size:7px">Bidhollow</span>
<div class="abs badge"></div>
<div class="abs social" style="left:453px">Hitch</div>
<div class="abs social" style="left:479px">Roper</div>
<div class="abs social" style="left:504px">Chirp</div>
<div class="abs social" style="left:530px">Dabble</div>
<div class="abs social" style="left:555px">Corral</div>
<div class="abs social" style="left:580px">Tack</div>

</body>
</html>
```